The most modern business card ever !!!

Our company call “Vendalo”. Vendalo is a technology company specialized in cruises solutions. Out main product is a platform to reserve cruises. This is a revolutionary platform that make easier to travel agencies and final users to reserve cruises across dozen companies like tibba, wernu, hpv, dgb, etc..We are a “start up”, with a young team of developers and we want to transmit it.. For it, we want something different, a modern business card that represent cruises and technology.. When someone receive this card, this person should say: wowww this is different… this is modern… this is a cruise related company..
- diferent, modern
- traditions business card

```html
<!DOCTYPE html>
<html lang="en">
<head>
<meta charset="utf-8">
<title>Vendalo Business Card</title>
<link href="https://fonts.googleapis.com/css2?family=Arimo:wght@400;700&family=Lato:wght@700;900&display=swap" rel="stylesheet">
<style>
  :root {
    --backdrop: #7a4a26;
    --card-front: #29a9e1;
    --card-back: #000000;
    --ink-light: #ffffff;
    --card-shadow: rgba(0, 0, 0, 0.45);
  }
  * { margin: 0; padding: 0; box-sizing: border-box; }
  html, body {
    width: 1200px;
    height: 900px;
    overflow: hidden;
    background: var(--backdrop);
  }
  .canvas {
    position: relative;
    width: 1200px;
    height: 900px;
  }
  .card {
    position: absolute;
    box-shadow: 3px 4px 6px var(--card-shadow);
  }
  .card--front {
    left: 329px;
    top: 90px;
    width: 556px;
    height: 343px;
    background: var(--card-front);
    color: var(--ink-light);
    text-align: center;
    font-family: "Arimo", Arial, sans-serif;
  }
  .card--back {
    left: 329px;
    top: 469px;
    width: 560px;
    height: 344px;
    background: var(--card-back);
  }
  .holder {
    position: absolute;
    left: 0;
    right: 0;
    top: 62px;
  }
  .holder__name {
    font-family: "Lato", Arial, sans-serif;
    font-weight: 900;
    font-size: 20px;
    line-height: 24px;
    letter-spacing: 0.2px;
  }
  .holder__role {
    font-size: 16px;
    line-height: 20px;
  }
  .divider {
    position: absolute;
    left: 181px;
    width: 195px;
    height: 1px;
    background: var(--ink-light);
  }
  .divider--upper { top: 116px; }
  .divider--lower { top: 221px; }
  .contact-list {
    position: absolute;
    left: 0;
    right: 0;
    top: 129px;
    list-style: none;
    font-size: 16px;
    line-height: 20px;
  }
  .contact-list b { font-weight: 700; }
  .address {
    position: absolute;
    left: 0;
    right: 0;
    top: 239px;
    font-size: 16px;
    line-height: 20px;
    font-style: normal;
  }
  .brand-name {
    position: absolute;
    left: 0;
    right: 0;
    top: 138px;
    text-align: center;
    font-family: "Lato", Arial, sans-serif;
    font-weight: 700;
    font-size: 64px;
    line-height: 70px;
    letter-spacing: 2px;
    color: var(--ink-light);
  }
</style>
</head>
<body>
  <main class="canvas">
    <section class="card card--front" aria-label="Card front">
      <header class="holder">
        <h1 class="holder__name">MARLON AVERY</h1>
        <p class="holder__role">Managing Director</p>
      </header>
      <div class="divider divider--upper"></div>
      <ul class="contact-list">
        <li><b>P:</b> 044-123 456 789</li>
        <li><b>M:</b> 044-123 456 789</li>
        <li><b>E:</b> info@webname.com</li>
        <li><b>W:</b> www.websitename.com</li>
      </ul>
      <div class="divider divider--lower"></div>
      <address class="address">
        12345, Address Goes Here<br>
        Country Name, 123456.
      </address>
    </section>

    <section class="card card--back" aria-label="Card back">
      <p class="brand-name">Vendalo</p>
    </section>
  </main>
</body>
</html>
```